English and Spanish Language School Needs a Business Card

Need a business card design a startup company called Maribel Language School. The company will offer English and Spanish conversational level courses designed to make the learner feel comfortable with grammar and vocabulary. We would like to see a logo with some colour that should communicate learning, growth.

Target Market(s)

Consumers and businesses

Industry/Entity Type

Education

Contact Information for Business Card

TBD

Font styles to use
Serif

Requirements
Must have
• Include the following
• Logo
• Name
• Title
• Cellphone Number
• Office Phone number
• Email address
• Office Address

```html
<!DOCTYPE html>
<html lang="en">
<head>
<meta charset="utf-8">
<title>Maribel Language School – Business Card</title>
<link href="https://fonts.googleapis.com/css2?family=Tinos:wght@400;700&display=swap" rel="stylesheet">
<style>
  :root {
    --brand-red: #c8202e;
    --brand-red-light: #d92a37;
    --brand-teal: #14b5bd;
    --card-white: #f7f7f7;
    --ink-grey: #8a8a8a;
    --stage: #e7e4df;
  }
  * { margin: 0; padding: 0; box-sizing: border-box; }
  html, body { width: 1200px; height: 780px; overflow: hidden; }
  body {
    background: var(--stage);
    font-family: "Tinos", "Times New Roman", serif;
    position: relative;
  }
  .card {
    position: absolute;
    top: 240px;
    width: 520px;
    height: 300px;
    overflow: hidden;
    box-shadow: 0 10px 24px rgba(0,0,0,0.18);
  }
  .card-front { left: 50px; background: var(--card-white); }
  .card-back {
    left: 630px;
    background: radial-gradient(circle at 50% 50%, var(--brand-red-light) 0 120px, var(--brand-red) 121px);
  }
  .front-shape { position: absolute; inset: 0; }
  .brand-name {
    position: absolute;
    font-weight: 700;
    line-height: 1;
  }
  .card-front .brand-name {
    left: 34px; top: 96px;
    color: var(--brand-red);
    font-size: 46px;
  }
  .brand-name small {
    display: block;
    font-size: 17px;
    font-weight: 700;
    margin-top: 4px;
    letter-spacing: 0.5px;
  }
  .card-back .brand-name {
    left: 0; right: 0; top: 110px;
    text-align: center;
    color: #ffffff;
    font-size: 56px;
  }
  .card-back .brand-name small { font-size: 19px; }
  .contact {
    position: absolute;
    left: 34px; top: 170px;
    color: var(--ink-grey);
    font-size: 12.5px;
    line-height: 1.25;
  }
  .person-name { color: var(--brand-red); font-size: 15px; letter-spacing: 0.5px; }
  .person-title { margin-bottom: 8px; }
  .address { margin-bottom: 8px; }
  .contact-line { display: flex; align-items: center; gap: 6px; }
  .contact-icon { width: 12px; height: 12px; flex: none; }
</style>
</head>
<body>

<section class="card card-front" aria-label="Business card front">
  <svg class="front-shape" viewBox="0 0 520 300" preserveAspectRatio="none" aria-hidden="true">
    <rect width="520" height="300" fill="var(--brand-red)"/>
    <path d="M0,300 L0,95 C140,30 360,20 460,130 C500,175 510,250 505,300 Z" fill="var(--card-white)"/>
    <path d="M0,82 C140,18 372,8 472,124" fill="none" stroke="var(--brand-teal)" stroke-width="3"/>
  </svg>

  <div class="brand-name">Maribel<small>Language School</small></div>

  <div class="contact">
    <div class="person-name">DANIEL REYES</div>
    <div class="person-title">Manager</div>
    <div class="address">48 Harlow Lane, 2nd Ste<br>Brookfield, Texas 7731</div>
    <div class="contact-line">
      <svg class="contact-icon" viewBox="0 0 12 12" aria-label="Cellphone"><rect width="12" height="12" fill="var(--brand-red)"/><rect x="4" y="2" width="4" height="8" rx="0.8" fill="none" stroke="#fff" stroke-width="1"/></svg>
      <span>555 014 2390</span>
    </div>
    <div class="contact-line">
      <svg class="contact-icon" viewBox="0 0 12 12" aria-label="Office phone"><rect width="12" height="12" fill="var(--brand-red)"/><path d="M2.5,5 Q6,2 9.5,5 L8.5,6 L7.5,5 L4.5,5 L3.5,6 Z M3.5,6.5 H8.5 V9.5 H3.5 Z" fill="#fff"/></svg>
      <span>555 014 2391</span>
    </div>
    <div class="contact-line">
      <svg class="contact-icon" viewBox="0 0 12 12" aria-label="Email"><rect width="12" height="12" fill="var(--brand-red)"/><rect x="2.5" y="3.5" width="7" height="5" fill="none" stroke="#fff" stroke-width="1"/><path d="M2.5,3.5 L6,6.5 L9.5,3.5" fill="none" stroke="#fff" stroke-width="1"/></svg>
      <span>hello@maribelschool.com</span>
    </div>
  </div>
</section>

<section class="card card-back" aria-label="Business card back">
  <div class="brand-name">Maribel<small>Language School</small></div>
</section>

</body>
</html>
```